Northfield Builders Guild Business card

We are looking for a new business card design with photo included.
Our business is a nonprofit construction contractor membership organization. We offer business education, assist with business setup and licensing, provide safety training, and provide a member directory.
URL: www.builderslinkguild.org
Color code:
CMYK: 0 cyan, 42 magenta, 100 yellow, 0 black for Print.
Hexidecimal: #FF9900
RGB: R 255; G 153; B 0

```html
<!DOCTYPE html>
<html lang="en">
<head>
<meta charset="utf-8">
<title>Northfield Builders Guild – Business Card</title>
<link href="https://fonts.googleapis.com/css2?family=Montserrat:wght@400;500;800&display=swap" rel="stylesheet">
<style>
  :root{
    --orange:#FF9900;
    --ink:#333333;
    --paper:#ffffff;
    --stage:#e9e7e3;
    --muted:#444444;
  }
  *{box-sizing:border-box;margin:0;padding:0}
  html,body{width:1200px;height:909px;overflow:hidden}
  body{background:var(--stage);font-family:"Montserrat",sans-serif;color:var(--ink);position:relative}
  .card{position:absolute;width:520px;height:300px;background:var(--paper);
        box-shadow:0 6px 18px rgba(0,0,0,.18);overflow:hidden}
  .card--front{left:70px;top:140px}
  .card--back{left:610px;top:470px}
  .card__wave{position:absolute;inset:0;width:100%;height:100%}
  .brand{display:flex;align-items:center;gap:8px}
  .brand__mark{width:12px;height:12px;background:var(--orange);flex:none}
  .brand__name{font-weight:800;color:var(--ink);text-transform:uppercase;letter-spacing:.5px;line-height:1.05}
  .card--front .brand{position:absolute;left:200px;top:100px}
  .card--front .brand__name{font-size:20px}
  .person{position:absolute;left:200px;top:160px}
  .person__name{color:var(--orange);font-weight:500;font-size:14px;letter-spacing:3px;text-transform:uppercase}
  .person__title{font-size:9.5px;color:var(--muted);margin-top:2px}
  .contacts{position:absolute;left:200px;top:204px;list-style:none}
  .contacts li{display:flex;align-items:center;gap:7px;font-size:10px;color:var(--muted);height:19px}
  .contacts svg{width:14px;height:14px;flex:none}
  .address{position:absolute;right:26px;top:26px;text-align:right;font-size:9.5px;line-height:1.45;color:var(--muted);font-style:normal}
  .card--back .brand{position:absolute;left:50%;top:50%;transform:translate(-50%,-50%);gap:10px}
  .card--back .brand__mark{width:16px;height:16px}
  .card--back .brand__name{font-size:25px}
</style>
</head>
<body>

<section class="card card--front">
  <svg class="card__wave" viewBox="0 0 520 300" aria-hidden="true">
    <path fill="var(--orange)" d="M0 0H330C260 20 190 50 140 110C100 160 70 230 55 300H0Z"/>
    <path fill="var(--ink)" d="M168 86C112 128 82 208 68 300H80C94 214 122 138 168 86Z"/>
  </svg>
  <div class="brand"><span class="brand__mark"></span><span class="brand__name">Northfield<br>Builders Guild</span></div>
  <div class="person">
    <p class="person__name">Dana Whitfield</p>
    <p class="person__title">CEO/Managing Director</p>
  </div>
  <ul class="contacts">
    <li><svg viewBox="0 0 14 14"><circle cx="7" cy="7" r="6.2" fill="none" stroke="var(--orange)"/><rect x="5" y="3.5" width="4" height="7" rx="0.8" fill="var(--orange)"/></svg>555-014-3920</li>
    <li><svg viewBox="0 0 14 14"><circle cx="7" cy="7" r="6.2" fill="none" stroke="var(--orange)"/><rect x="4" y="5" width="6" height="4.5" fill="var(--orange)"/><rect x="5" y="3.5" width="4" height="2" fill="var(--orange)"/></svg>555-014-3921</li>
    <li><svg viewBox="0 0 14 14"><circle cx="7" cy="7" r="6.2" fill="none" stroke="var(--orange)"/><rect x="3.8" y="4.6" width="6.4" height="4.8" fill="var(--orange)"/><path d="M3.8 4.6L7 7.4 10.2 4.6" fill="none" stroke="#fff" stroke-width=".8"/></svg>dana@builderslinkguild.org</li>
    <li><svg viewBox="0 0 14 14"><circle cx="7" cy="7" r="6.2" fill="none" stroke="var(--orange)"/><circle cx="7" cy="7" r="3.6" fill="none" stroke="var(--orange)" stroke-width=".9"/><path d="M3.4 7H10.6M7 3.4C5.5 5 5.5 9 7 10.6M7 3.4C8.5 5 8.5 9 7 10.6" fill="none" stroke="var(--orange)" stroke-width=".7"/></svg>www.builderslinkguild.org</li>
  </ul>
  <address class="address">118 Larkspur Street Suite 210<br>Northfield MN 55057</address>
</section>

<section class="card card--back">
  <div class="brand"><span class="brand__mark"></span><span class="brand__name">Northfield<br>Builders Guild</span></div>
</section>

</body>
</html>
```